Construction Company

Design a clutter free business card, it can be double-sided utilizing the logo for VKM Ltd simple with all relevant contact information.

Please also a letterhead design to function for the purposes of invoicing, all mail requirements, with header to be distinctive while the footer ties page together and incorporates all necessary information.

For now, please use generic / dummy text and when a winner is selected, I will disclose the contact information.

Hi Designers! Please read the updated brief which includes the design of a business card and letterhead. Thank you!

```html
<!DOCTYPE html>
<html lang="en">
<head>
<meta charset="utf-8">
<title>VKM Ltd – Stationery</title>
<link href="https://fonts.googleapis.com/css2?family=Libre+Baskerville:wght@400;700&family=Open+Sans:wght@400;600&display=swap" rel="stylesheet">
<style>
  :root{
    --navy:#27398f;
    --navy-deep:#1f2f7c;
    --gold:#b8962e;
    --paper:#ffffff;
    --ink:#3a3a3a;
    --muted:#8a8a8a;
    --backdrop:#ececec;
  }
  *{box-sizing:border-box;margin:0;padding:0}
  html,body{width:1200px;height:2342px;overflow:hidden;background:var(--backdrop)}
  body{font-family:"Open Sans",Arial,sans-serif;color:var(--ink);position:relative}
  .section{position:absolute;left:0;width:1200px}
  .section--cards{top:0;height:800px}
  .section--letters{top:800px;height:740px;background:#e6e6e6}
  .section--envelopes{top:1540px;height:802px}

  .brand{font-family:"Libre Baskerville",Georgia,serif;font-weight:400;color:var(--navy);letter-spacing:1px;white-space:nowrap}
  .brand--light{color:var(--paper)}

  .icon{width:1em;height:1em;fill:currentColor;vertical-align:-0.12em;margin-right:.4em}

  /* Business cards */
  .card{position:absolute;width:520px;height:297px;box-shadow:0 8px 24px rgba(0,0,0,.15)}
  .card--front{left:50px;top:250px;background:var(--paper);border-bottom:3px solid var(--gold)}
  .card--back{left:630px;top:250px;background:var(--navy);border-bottom:3px solid var(--gold);overflow:hidden}
  .card__brand{position:absolute;left:40px;top:110px;font-size:38px}
  .card__divider{position:absolute;left:250px;top:70px;width:1px;height:120px;background:var(--navy)}
  .card__details{position:absolute;left:272px;top:70px}
  .card__name{font-family:"Libre Baskerville",Georgia,serif;font-weight:700;font-size:20px;color:var(--navy);text-transform:uppercase}
  .card__role{font-size:14px;font-weight:600;color:var(--gold);margin:2px 0 14px}
  .card__line{font-size:15px;color:var(--navy);line-height:1.45}
  .card__band{position:absolute;left:0;bottom:0;width:100%;height:34px;background:var(--navy);display:flex;align-items:center;padding-left:26px;color:var(--paper);font-size:15px}
  .card__band-accent{position:absolute;right:0;top:0;width:80px;height:100%;background:var(--gold)}
  .card__pattern{position:absolute;inset:0;background:radial-gradient(circle at 50% 50%,#2d41a0,var(--navy-deep))}
  .card__back-brand{position:absolute;right:60px;top:150px;font-size:44px}

  /* Letterheads */
  .letter{position:absolute;top:80px;width:420px;height:580px;background:var(--paper);box-shadow:0 6px 18px rgba(0,0,0,.15)}
  .letter--one{left:150px}
  .letter--two{left:630px}
  .letter__brand{position:absolute;left:36px;top:48px;font-size:26px}
  .letter__contact{position:absolute;right:36px;top:50px;font-size:8.5px;color:var(--navy);line-height:1.35}
  .letter__body{position:absolute;left:36px;right:36px;top:150px;font-size:6.4px;color:var(--muted);line-height:1.55}
  .letter__body p{margin-bottom:8px}
  .letter__signature{width:50px;height:38px;background:linear-gradient(135deg,#ddd,#f4f4f4);margin-top:8px}
  .letter__footer{position:absolute;left:0;bottom:20px;width:100%;height:14px;background:var(--navy);color:var(--paper);font-size:8px;display:flex;align-items:center;justify-content:center}
  .letter__footer-accent{position:absolute;right:0;top:0;width:40px;height:100%;background:var(--gold)}

  /* Envelopes */
  .envelope{position:absolute;width:620px;height:310px;background:var(--paper);box-shadow:0 8px 22px rgba(0,0,0,.13);overflow:hidden}
  .envelope--back{left:290px;top:40px}
  .envelope--front{left:290px;top:420px}
  .envelope__flap{position:absolute;left:0;top:0;width:100%;height:120px}
  .envelope__flap-brand{position:absolute;left:0;top:44px;width:100%;text-align:center;font-size:34px}
  .envelope__brand{position:absolute;left:40px;top:40px;font-size:36px}
  .envelope__contact{position:absolute;left:40px;top:150px;font-size:16px;color:var(--navy);line-height:1.35}
  .envelope__band{position:absolute;left:0;bottom:36px;width:100%;height:32px;background:var(--navy);color:var(--paper);font-size:16px;display:flex;align-items:center;padding-left:30px}
  .envelope__band-accent{position:absolute;right:0;top:0;width:90px;height:100%;background:var(--gold)}
</style>
</head>
<body>
<svg width="0" height="0" style="position:absolute" aria-hidden="true">
  <symbol id="i-phone" viewBox="0 0 24 24"><path d="M6.6 10.8a15.1 15.1 0 0 0 6.6 6.6l2.2-2.2a1 1 0 0 1 1-.25 11.4 11.4 0 0 0 3.6.57 1 1 0 0 1 1 1V20a1 1 0 0 1-1 1A17 17 0 0 1 3 4a1 1 0 0 1 1-1h3.5a1 1 0 0 1 1 1c0 1.25.2 2.45.57 3.57a1 1 0 0 1-.25 1z"/></symbol>
  <symbol id="i-mail" viewBox="0 0 24 24"><path d="M2 5h20v14H2z M3.5 6.5 12 13l8.5-6.5" fill="currentColor"/><path d="M3 6l9 7 9-7" fill="none" stroke="#fff" stroke-width="1.6"/></symbol>
  <symbol id="i-globe" viewBox="0 0 24 24"><circle cx="12" cy="12" r="10"/><path d="M2 12h20M12 2c3 3 3 17 0 20M12 2c-3 3-3 17 0 20" fill="none" stroke="#fff" stroke-width="1.3"/></symbol>
  <symbol id="i-pin" viewBox="0 0 24 24"><path d="M12 2a7 7 0 0 0-7 7c0 5 7 13 7 13s7-8 7-13a7 7 0 0 0-7-7zm0 9.5A2.5 2.5 0 1 1 12 6.5a2.5 2.5 0 0 1 0 5z"/></symbol>
</svg>

<section class="section section--cards">
  <article class="card card--front">
    <div class="brand card__brand">VKM Ltd</div>
    <div class="card__divider"></div>
    <div class="card__details">
      <div class="card__name">Daniel Ward</div>
      <div class="card__role">Director</div>
      <div class="card__line"><svg class="icon"><use href="#i-phone"/></svg>949.555.0142</div>
      <div class="card__line"><svg class="icon"><use href="#i-mail"/></svg>dan@vkmltd.com</div>
      <div class="card__line"><svg class="icon"><use href="#i-globe"/></svg>www.vkmltd.com</div>
    </div>
    <div class="card__band"><svg class="icon"><use href="#i-pin"/></svg>Harbour Court, 12 Mill Lane, London, SE4 2RT<span class="card__band-accent"></span></div>
  </article>
  <article class="card card--back">
    <div class="card__pattern" role="img" aria-label="Embossed repeating flower pattern in deep blue"></div>
    <div class="brand brand--light card__back-brand">VKM Ltd</div>
  </article>
</section>

<section class="section section--letters">
  <article class="letter letter--one">
    <div class="brand letter__brand">VKM Ltd</div>
    <div class="letter__contact">
      <div><svg class="icon"><use href="#i-phone"/></svg>949.555.0142</div>
      <div><svg class="icon"><use href="#i-mail"/></svg>dan@vkmltd.com</div>
      <div><svg class="icon"><use href="#i-globe"/></svg>www.vkmltd.com</div>
    </div>
    <div class="letter__body">
      <p>Dear customer,</p>
      <p>Thank you for choosing us for your next building project. This page shows where the body of a letter or invoice will sit, set in a calm size with generous line spacing for easy reading.</p>
      <p>Thank you for choosing us for your next building project. This page shows where the body of a letter or invoice will sit, set in a calm size with generous line spacing for easy reading.</p>
      <p>Thank you for choosing us for your next building project. This page shows where the body of a letter or invoice will sit, set in a calm size with generous line spacing for easy reading.</p>
      <p>Thank you for choosing us for your next building project. This page shows where the body of a letter or invoice will sit, set in a calm size with generous line spacing for easy reading.</p>
      <p>Yours sincerely,</p>
      <div class="letter__signature" role="img" aria-label="Handwritten signature"></div>
    </div>
    <div class="letter__footer"><svg class="icon"><use href="#i-pin"/></svg>Harbour Court, 12 Mill Lane, London, SE4 2RT<span class="letter__footer-accent"></span></div>
  </article>
  <article class="letter letter--two">
    <div class="brand letter__brand">VKM Ltd</div>
    <div class="letter__contact">
      <div><svg class="icon"><use href="#i-phone"/></svg>949.555.0142</div>
      <div><svg class="icon"><use href="#i-mail"/></svg>dan@vkmltd.com</div>
      <div><svg class="icon"><use href="#i-globe"/></svg>www.vkmltd.com</div>
    </div>
    <div class="letter__body">
      <p>Dear customer,</p>
      <p>Thank you for choosing us for your next building project. This page shows where the body of a letter or invoice will sit, set in a calm size with generous line spacing for easy reading.</p>
      <p>Thank you for choosing us for your next building project. This page shows where the body of a letter or invoice will sit, set in a calm size with generous line spacing for easy reading.</p>
      <p>Thank you for choosing us for your next building project. This page shows where the body of a letter or invoice will sit, set in a calm size with generous line spacing for easy reading.</p>
      <p>Thank you for choosing us for your next building project. This page shows where the body of a letter or invoice will sit, set in a calm size with generous line spacing for easy reading.</p>
      <p>Yours sincerely,</p>
      <div class="letter__signature" role="img" aria-label="Handwritten signature"></div>
    </div>
    <div class="letter__footer"><svg class="icon"><use href="#i-pin"/></svg>Harbour Court, 12 Mill Lane, London, SE4 2RT<span class="letter__footer-accent"></span></div>
  </article>
</section>

<section class="section section--envelopes">
  <article class="envelope envelope--back">
    <svg class="envelope__flap" viewBox="0 0 620 120" preserveAspectRatio="none" aria-hidden="true">
      <path d="M0 0H620V40Q610 60 590 62L0 120Z" fill="var(--navy)"/>
    </svg>
    <div class="brand brand--light envelope__flap-brand">VKM Ltd</div>
  </article>
  <article class="envelope envelope--front">
    <div class="brand envelope__brand">VKM Ltd</div>
    <div class="envelope__contact">
      <div><svg class="icon"><use href="#i-phone"/></svg>949.555.0142</div>
      <div><svg class="icon"><use href="#i-mail"/></svg>dan@vkmltd.com</div>
      <div><svg class="icon"><use href="#i-globe"/></svg>www.vkmltd.com</div>
    </div>
    <div class="envelope__band"><svg class="icon"><use href="#i-pin"/></svg>Harbour Court, 12 Mill Lane, London, SE4 2RT<span class="envelope__band-accent"></span></div>
  </article>
</section>
</body>
</html>
```